Business Card Design needed - Something Awesome!

Need a business card designed. Company is "Marlowe Advisory" we do consulting and also have sales automation technology.
I'm going to use thick stock or metal, something really nice... I was thinking about a QR Code on the back that would just upload my contact info to the persons contact, etc -

This is a Strategy Company with a tech feel. I'm open to ideas but really want this to be nice!

I need a template that should include:

Name | Position or Title
D: 415.902.3376
www.marloweadvisory.example

I'm going to attach my contact so you can use that one, I need to get this printed.

Target Market(s)

Small to mid size customers, Entrepreneurs etc.

Industry/Entity Type

Consulting, Tech, Private Equity.

Contact Information for Business Card

Name, Phone, Maybe email, URL

Font styles to use
Sans Serif

Colors

Designer to choose only greyscale colors for use in the design.

Requirements
Must have
• Fresh, Clean, stand out from the crowd - will be on thick stock or metal.
Nice to have
• Clean, simple yet impactful.
Should not have
• Not cartoonish

```html
<!DOCTYPE html>
<html lang="en">
<head>
<meta charset="utf-8">
<title>Marlowe Advisory — Business Card</title>
<link href="https://fonts.googleapis.com/css2?family=Roboto:wght@300;400;500;700&display=swap" rel="stylesheet">
<style>
  :root {
    --backdrop: #3a3a3a;
    --card: #141414;
    --silver: #cfcfcf;
    --silver-soft: #a9a9a9;
    --divider: #6a6a6a;
    --gloss: #262626;
  }
  * { margin: 0; padding: 0; box-sizing: border-box; }
  html, body {
    width: 1200px; height: 801px; overflow: hidden;
    background: var(--backdrop);
    font-family: "Roboto", sans-serif;
  }
  .stage {
    width: 1200px; height: 801px;
    display: flex; align-items: center; justify-content: center; gap: 48px;
  }
  .card {
    position: relative;
    width: 532px; height: 304px;
    background: var(--card);
    box-shadow: 0 10px 30px rgba(0,0,0,.45);
  }
  .wordmark {
    font-weight: 500;
    letter-spacing: 1px;
    text-transform: uppercase;
    display: flex; align-items: center; gap: 10px;
    white-space: nowrap;
  }
  .wordmark-square { width: 14px; height: 14px; background: currentColor; }

  .card-front .wordmark {
    position: absolute; left: 42px; top: 62px;
    font-size: 31px; color: var(--silver);
  }
  .holder {
    position: absolute; left: 42px; bottom: 52px; text-align: right;
  }
  .holder-name {
    font-weight: 700; font-size: 16px; letter-spacing: .5px;
    color: var(--silver); text-transform: uppercase;
  }
  .holder-title {
    font-weight: 400; font-size: 14px; color: var(--silver-soft); margin-top: 4px;
  }
  .divider {
    position: absolute; left: 240px; bottom: 46px;
    width: 1px; height: 52px; background: var(--divider);
  }
  .contacts {
    position: absolute; left: 258px; bottom: 46px;
    list-style: none; color: var(--silver-soft);
    font-size: 12.5px; font-weight: 300; line-height: 17px;
  }
  .contacts li { display: flex; align-items: center; gap: 7px; }
  .contacts svg { width: 10px; height: 10px; fill: var(--silver); flex: none; }

  .card-back .wordmark {
    position: absolute; left: 50%; top: 50%;
    transform: translate(-50%, -50%);
    font-size: 40px; color: var(--gloss);
  }
</style>
</head>
<body>
<main class="stage">
  <section class="card card-front" aria-label="Card front">
    <div class="wordmark">Marlowe Advisory <span class="wordmark-square"></span></div>
    <div class="holder">
      <p class="holder-name">Adrian K. Vossel</p>
      <p class="holder-title">Founder / CEO</p>
    </div>
    <span class="divider"></span>
    <ul class="contacts">
      <li><svg viewBox="0 0 10 10"><path d="M2 0.5l1.6 2.2-1 1c.6 1.3 1.5 2.2 2.8 2.8l1-1L8.6 7.1 7.8 9C4 8.6 1.3 6 1 2.2z"/></svg>415.902.3376</li>
      <li><svg viewBox="0 0 10 10"><path d="M0 2h10v6H0z M0 2l5 3.3L10 2" stroke="#141414" stroke-width=".8"/></svg>info@marloweadvisory.example</li>
      <li><svg viewBox="0 0 10 10"><circle cx="5" cy="5" r="4.5"/><path d="M.5 5h9M5 .5c-2.4 2.6-2.4 6.4 0 9M5 .5c2.4 2.6 2.4 6.4 0 9" stroke="#141414" stroke-width=".7" fill="none"/></svg>www.marloweadvisory.example</li>
    </ul>
  </section>

  <section class="card card-back" aria-label="Card back">
    <div class="wordmark">Marlowe Advisory <span class="wordmark-square"></span></div>
  </section>
</main>
</body>
</html>
```